Marwick Biomedical Research Institute (MBRI) Web Design

MBRI is a non-profit organization focused on saving the lives of terminally ill patients by becoming the leaders in cutting-edge research, innovative technologies, utilizing national and international partnerships as well as the associated allopathic and naturopathic treatments necessary to do so.

Our primary focus is raising funds to support the research and acquisition of new technologies for life saving treatments which are NOT a one size fits all approach like conventional medicine but rather a marriage of the latest technologies used in combination with other new treatment possibilities for a successful end result.

Our domain is marwickbri.org

Logo files are attached.

Looking for something clean, light, healthy.

Target Market(s)

The site should look and feel towards research/scientific grant writing.
Medical professionals, Medical Scientists.

Industry/Entity Type

Medical And Science

Number of Pages Required

4 page

Requirements
Nice to have
• Here are examples of sites I like in the order of how much I like them.
• https://www.palvorn.org/give.html
• https://www.thekqtf.org/donate-to-kqtf
• https://www.veltrasound.org/we-are-vsf/join-the-cause
• https://www.orvenly.org/involved/donate.html
• https://give.zdkt.org/checkout/donation?eid=58217
• https://www.quimbrel.org/how-you-can-help
• https://donate3.orvenly.org/

```html
<!DOCTYPE html>
<html lang="en">
<head>
<meta charset="utf-8">
<title>Marwick Biomedical Research Institute</title>
<link rel="stylesheet" href="https://fonts.googleapis.com/css2?family=Lato:wght@400;700;900&display=swap">
<style>
:root{
  --blue:#1a7bc0;
  --blue-dark:#125c9c;
  --green:#3f9a3a;
  --green-light:#6cbb3c;
  --text:#333;
  --muted:#8a8a8a;
  --pink:#e2458a;
  --white:#fff;
}
*{box-sizing:border-box;margin:0;padding:0}
html,body{width:1200px;height:3409px;overflow:hidden}
body{font-family:'Lato',sans-serif;color:var(--text);background:var(--white);position:relative}
.abs{position:absolute}
a{color:inherit;text-decoration:none}

/* header */
.site-header{position:absolute;top:0;left:0;width:1200px;height:102px;background:var(--white)}
.brand{position:absolute;left:92px;top:28px;width:250px;font-size:18px;line-height:23px;font-weight:400;color:var(--text)}
.main-nav{position:absolute;left:411px;top:9px;display:flex;align-items:center;gap:24px;font-size:16px;color:#444}
.main-nav .active{width:80px;height:80px;border-radius:50%;background:var(--blue);color:var(--white);display:flex;align-items:center;justify-content:center}

/* hero */
.hero{position:absolute;top:102px;left:0;width:1200px;height:557px;background:radial-gradient(circle at 38% 30%,#5c9a9a 0,#2f6c76 30%,#1d4a57 65%,#163a47 100%)}
.hero-kicker{position:absolute;top:178px;width:100%;text-align:center;font-size:28px;font-weight:700;color:var(--white);letter-spacing:.5px}
.hero-title{position:absolute;top:216px;width:100%;text-align:center;font-size:44px;font-weight:700;color:var(--white)}
.btn-ghost{position:absolute;left:520px;top:276px;width:156px;height:50px;border:2px solid var(--white);border-radius:25px;color:var(--white);font-size:16px;display:flex;align-items:center;justify-content:center}
.dots{position:absolute;left:552px;top:494px;display:flex;gap:10px}
.dots span{width:12px;height:12px;border-radius:50%;background:rgba(255,255,255,.45)}
.dots span.on{background:rgba(255,255,255,.85)}

/* welcome */
.welcome-photo{position:absolute;left:109px;top:652px;width:386px;height:386px;border-radius:50%;background:radial-gradient(circle at 50% 45%,#e9eef1,#c9d6de);border:6px solid #eef2f4}
.welcome h2{position:absolute;left:530px;top:716px;font-size:32px;font-weight:700;color:var(--blue-dark);line-height:1.35}
.welcome h2 span{color:var(--green)}
.welcome p{position:absolute;left:528px;width:490px;font-size:16px;line-height:1.75;color:var(--muted)}
.btn-outline{position:absolute;left:527px;top:994px;width:156px;height:48px;border:2px solid var(--green);border-radius:24px;color:var(--green);font-size:16px;display:flex;align-items:center;justify-content:center}

/* mission */
.mission{position:absolute;top:1118px;left:0;width:1200px;height:473px;background:linear-gradient(90deg,#1b6fb3,#2a8fd1)}
.mission-photo{position:absolute;left:0;top:0}
.mission h2{position:absolute;left:98px;top:98px;font-size:30px;font-weight:700;color:var(--white)}
.mission p{position:absolute;left:98px;width:420px;font-size:15px;line-height:1.75;color:#d7e9f7}
.btn-solid{position:absolute;border-radius:24px;color:var(--white);font-size:16px;display:flex;align-items:center;justify-content:center}
.mission .btn-solid{left:98px;top:320px;width:154px;height:46px;background:#2d97e0}

/* features */
.features{position:absolute;top:1591px;left:0;width:1200px;height:511px;background:#f6f8fa}
.card{position:absolute;top:57px;width:330px;height:375px;background:var(--white);box-shadow:0 2px 10px rgba(0,0,0,.08);text-align:center}
.card-photo{display:block;width:330px;height:210px}
.card h3{margin-top:22px;font-size:21px;font-weight:700;color:#222}
.card p{margin:12px auto 0;width:270px;font-size:14px;line-height:1.6;color:var(--muted)}
.card a{display:inline-block;margin-top:14px;font-size:13px;font-weight:700;color:var(--blue-dark);text-decoration:underline}

/* naturopathic */
.natural{position:absolute;top:2102px;left:0;width:1200px;height:478px;background:linear-gradient(120deg,#d9b8e4 0,#b678c4 35%,#e7d5ea 65%,#caa2d3 100%)}
.natural-panel{position:absolute;left:607px;top:75px;width:507px;height:300px;background:rgba(255,255,255,.92);padding:40px 54px}
.natural-panel h2{font-size:30px;font-weight:700;color:#333}
.natural-panel p{margin-top:14px;font-size:15px;line-height:1.6;color:var(--muted)}
.natural-panel .btn-solid{position:static;margin-top:16px;width:148px;height:46px;background:var(--green)}

/* blogs */
.blogs h2{position:absolute;left:95px;top:2626px;font-size:34px;font-weight:400;color:var(--blue-dark)}
.blog-thumb{position:absolute;top:2696px;width:190px;height:190px;border-radius:50%;border:5px solid #e6e6e6}
.blog-text{position:absolute;top:2720px;width:290px}
.blog-text h3{font-size:17px;font-weight:400;line-height:1.45;color:#222}
.blog-text p{margin-top:8px;font-size:12px;line-height:1.55;color:var(--muted)}
.blog-text a{display:block;margin-top:8px;font-size:13px;color:var(--pink)}

/* footer */
.site-footer{position:absolute;top:2900px;left:0;width:1200px;height:509px}
.footer-col{position:absolute;top:165px}
.footer-col h4{font-size:24px;font-weight:400;color:var(--white)}
.footer-col ul{list-style:none;margin-top:24px}
.footer-col li{font-size:16px;color:var(--white);line-height:35px}
.footer-divider{position:absolute;top:170px;width:1px;height:160px;background:rgba(255,255,255,.35)}
.social{display:flex;gap:12px;margin-top:24px}
.social span{width:42px;height:42px;border-radius:50%;border:2px solid var(--white)}
.copyright{position:absolute;top:466px;width:100%;text-align:center;font-size:14px;color:var(--white)}
</style>
</head>
<body>

<header class="site-header">
  <a class="brand" href="#">Marwick Biomedical Research Institute</a>
  <nav class="main-nav">
    <a class="active" href="#">Home</a>
    <a href="#">About Us</a>
    <a href="#">Services</a>
    <a href="#">Why Us</a>
    <a href="#">Our Patients</a>
    <a href="#">Research</a>
    <a href="#">Contact Us</a>
  </nav>
</header>

<section class="hero" role="img" aria-label="Microscopic view of a cell">
  <div class="hero-kicker">ETIAM URNA SED PORTA SUSPENDISSE</div>
  <h1 class="hero-title">BIO MEDICAL RESEARCH &amp; TREATMENT</h1>
  <a class="btn-ghost" href="#">Learn More</a>
  <div class="dots"><span></span><span></span><span class="on"></span><span></span></div>
</section>

<section class="welcome">
  <div class="welcome-photo" role="img" aria-label="Researcher examining a plant sample in the lab"></div>
  <h2>Welcome to <span>Marwick Biomedical</span><br><span>Research Institute</span></h2>
  <p style="top:813px">Vivamus porttitor purus nisi eleifend libero a tempus libero lectus feugiat felis vlacus Ut ac mi quis lacus</p>
  <p style="top:882px">mollis aliquam Curabitur iaculis tempus eros Curabitur vel mi sit amet magna malesuada ultrices Ut nisi erat fermentum vel congue id euismod in elit Fusce ultricies orci ac feugiat</p>
  <a class="btn-outline" href="#">Learn More</a>
</section>

<section class="mission">
  <svg class="mission-photo" width="1200" height="473" viewBox="0 0 1200 473" role="img" aria-label="Nurse caring for a patient in a hospital bed">
    <defs><linearGradient id="wardTone" x1="0" y1="0" x2="1" y2="1"><stop offset="0" stop-color="#dfe7ec"/><stop offset="1" stop-color="#9fb8c6"/></linearGradient></defs>
    <path d="M530 473 C520 300 560 110 720 0 L1200 0 L1200 473 Z" fill="url(#wardTone)"/>
  </svg>
  <h2>Our Mission</h2>
  <p style="top:152px">Vivamus porttitor purus nisi eleifend libero a tempus libero lectus feugiat felis vlacus Ut ac mi quis lacus mollis aliquam Curabitur iaculis tempus</p>
  <p style="top:246px">feugiat felis Morbi diam mauris viverr feugiat felis Morbi diam mauris viverra in gravida eu</p>
  <a class="btn-solid" href="#">Click here</a>
</section>

<section class="features">
  <article class="card" style="left:86px">
    <svg class="card-photo" viewBox="0 0 330 210" role="img" aria-label="Laboratory microscope with samples"><rect width="330" height="210" fill="#7fa9b8"/><path d="M0 175 Q165 215 330 165 V210 H0Z" fill="#3f9a3a"/><path d="M0 185 Q165 225 330 178 V210 H0Z" fill="#fff"/></svg>
    <h3>Innovative Technologies</h3>
    <p>feugiat felis Morbi diam mauris viverra in gravida eu mattis in ante Morbi</p>
    <a href="#">Learn More »</a>
  </article>
  <article class="card" style="left:439px">
    <svg class="card-photo" viewBox="0 0 330 210" role="img" aria-label="Scientist working at a microscope"><rect width="330" height="210" fill="#a6c3d6"/><path d="M0 175 Q165 215 330 165 V210 H0Z" fill="#1a6fb3"/><path d="M0 185 Q165 225 330 178 V210 H0Z" fill="#fff"/></svg>
    <h3>Our Research</h3>
    <p>feugiat felis Morbi diam mauris viverra in gravida eu mattis in ante Morbi</p>
    <a href="#">Learn More »</a>
  </article>
  <article class="card" style="left:791px">
    <svg class="card-photo" viewBox="0 0 330 210" role="img" aria-label="Elderly patient resting in bed"><rect width="330" height="210" fill="#cfc9c2"/><path d="M0 175 Q165 215 330 165 V210 H0Z" fill="#3f9a3a"/><path d="M0 185 Q165 225 330 178 V210 H0Z" fill="#fff"/></svg>
    <h3>Help Patients</h3>
    <p>feugiat felis Morbi diam mauris viverra in gravida eu mattis in ante Morbi</p>
    <a href="#">Learn More »</a>
  </article>
</section>

<section class="natural" role="img" aria-label="Dropper over an amber bottle among purple blossoms">
  <div class="natural-panel">
    <h2>Naturopathic Treatment</h2>
    <p>Vivamus porttitor purus nisi eleifend libero a tempus libero lectus feugiat felis vlacus Ut ac mi quis lacus mollis aliquam Curabitur iaculis tempus</p>
    <p style="margin-top:10px">Etiam eu urna Sed porta Suspendisse quam</p>
    <a class="btn-solid" href="#">Click here</a>
  </div>
</section>

<section class="blogs">
  <h2>Recent&nbsp; Blogs</h2>
  <div class="blog-thumb" style="left:91px;background:radial-gradient(circle,#5fa7c8,#1c5d88)" role="img" aria-label="DNA strand illustration"></div>
  <div class="blog-text" style="left:293px">
    <h3>Etiam eu urna Sed porta Suspe ndisse quam leo molest</h3>
    <p>netus et malesuada fames ac turpis egestas Cras id elit integer aptent lacus fringilla eu condimentum quis tellus aenean porttitor eros vel</p>
    <a href="#">READ MORE</a>
  </div>
  <div class="blog-thumb" style="left:621px;background:radial-gradient(circle,#cfe4f0,#7fb2cf)" role="img" aria-label="Researcher holding test tubes"></div>
  <div class="blog-text" style="left:823px">
    <h3>Mauris vel lacus vitae felis vestibulum volutpat</h3>
    <p>netus et malesuada fames ac turpis egestas Cras id elit integer aptent lacus fringilla eu condimentum quis tellus aenean porttitor eros vel</p>
    <a href="#">READ MORE</a>
  </div>
</section>

<footer class="site-footer">
  <svg class="abs" style="left:0;top:0" width="1200" height="509" viewBox="0 0 1200 509" aria-hidden="true">
    <defs><linearGradient id="footTone" x1="0" y1="0" x2="0" y2="1"><stop offset="0" stop-color="#3f9a48"/><stop offset="1" stop-color="#17708c"/></linearGradient></defs>
    <path d="M0 40 Q600 125 1200 30 V509 H0Z" fill="url(#footTone)"/>
  </svg>
  <div class="footer-col" style="left:107px"><h4>Quick Links</h4><ul><li>Home</li><li>About Us</li><li>What We Do</li><li>Why Us</li></ul></div>
  <div class="footer-divider" style="left:295px"></div>
  <div class="footer-col" style="left:357px;top:162px"><h4>Sublinks</h4><ul><li>Cancer Patients</li><li>Donate Now</li><li>Success Stories</li><li>Blogs</li></ul></div>
  <div class="footer-divider" style="left:550px"></div>
  <div class="footer-col" style="left:623px;top:160px"><h4>Resources</h4><ul><li>Sitemap</li><li>Term of Use</li><li>Contact Us</li></ul></div>
  <div class="footer-divider" style="left:798px"></div>
  <div class="footer-col" style="left:864px;top:160px"><h4>Follow Us</h4><div class="social"><span></span><span></span><span></span><span></span></div></div>
  <div class="copyright">© 2017 Company Name &nbsp;All right reserved &nbsp;Term of Use</div>
</footer>

</body>
</html>
```